Business card for law firm

Need business card for new law firm. Think confident, authoritative, conservative, but not stuffy or old-fashioned.

Contact Information for Business Card

Content for card - logo (uploaded), plus the following:

Paul Whitcombe (larger font)
Managing Partner (larger font, but not as large as name)
Level 9, 7 Ferris Lane
Sydney NSW 2000
Main Tel 02 9364 2710
Direct Tel 02 8472 3159
Email paul@qvlegal.com.au
www.qvlegal.com.au

Letterhead design should include logo plus:
Level 9, 7 Ferris Lane
Sydney NSW 2000
Tel 02 8472 3159
www.qvlegal.com.au

```html
<!DOCTYPE html>
<html lang="en">
<head>
<meta charset="utf-8">
<title>Quayvale Legal — Business Card</title>
<link rel="stylesheet" href="https://fonts.googleapis.com/css2?family=Cinzel:wght@400;600&family=Open+Sans:wght@400&display=swap">
<style>
  :root {
    --backdrop: #3b3431;
    --card-white: #f7f7f6;
    --card-black: #111111;
    --navy: #10256a;
    --ink: #2b2b2b;
    --divider: #e2e2e0;
    --silver: #c8c8c8;
  }
  * { margin: 0; padding: 0; box-sizing: border-box; }
  html, body { width: 1200px; height: 844px; overflow: hidden; }
  body { background: var(--backdrop); position: relative; font-family: "Open Sans", Arial, sans-serif; }

  .card {
    position: absolute;
    width: 520px;
    height: 298px;
    border-radius: 2px;
    box-shadow: 0 12px 28px rgba(0,0,0,0.45);
  }

  /* Front side */
  .card-front { left: 60px; top: 330px; background: var(--card-white); }
  .front-brand {
    position: absolute; left: 0; top: 0; width: 250px; height: 100%;
    display: flex; flex-direction: column; align-items: center; justify-content: center; gap: 14px;
  }
  .brand-square { width: 18px; height: 18px; background: var(--navy); }
  .front-brand .brand-name {
    font-family: "Cinzel", Georgia, serif; font-weight: 600;
    font-size: 22px; letter-spacing: 1.5px; color: var(--navy); text-align: center; line-height: 1.25;
  }
  .front-divider {
    position: absolute; left: 262px; top: 40px; width: 1px; height: 218px; background: var(--divider);
  }
  .contact {
    position: absolute; left: 282px; top: 58px; color: var(--ink);
  }
  .contact .person-name {
    font-family: "Cinzel", Georgia, serif; font-weight: 600;
    font-size: 19px; color: var(--navy); letter-spacing: 0.5px; line-height: 1.1;
  }
  .contact .person-role { font-size: 14px; margin-bottom: 6px; }
  .contact-list { list-style: none; font-size: 13.5px; line-height: 1.45; }
  .contact-list li { display: flex; align-items: center; gap: 7px; }
  .contact-list svg { width: 11px; height: 11px; fill: var(--navy); flex: none; }
  .contact .address { font-size: 13.5px; line-height: 1.4; margin-top: 4px; }

  /* Back side */
  .card-back { left: 620px; top: 200px; background: var(--card-black); }
  .back-brand {
    position: absolute; inset: 0;
    display: flex; flex-direction: column; align-items: center; justify-content: center; gap: 22px;
  }
  .back-brand .brand-square { background: var(--silver); width: 22px; height: 22px; }
  .back-brand .brand-name {
    font-family: "Cinzel", Georgia, serif; font-weight: 600;
    font-size: 34px; letter-spacing: 4px; color: var(--silver);
  }
</style>
</head>
<body>

  <section class="card card-front">
    <div class="front-brand">
      <span class="brand-square"></span>
      <span class="brand-name">Quayvale<br>Legal</span>
    </div>
    <div class="front-divider"></div>
    <div class="contact">
      <p class="person-name">PAUL WHITCOMBE</p>
      <p class="person-role">Managing Partner</p>
      <ul class="contact-list">
        <li><svg viewBox="0 0 12 12"><path d="M1 4.5C1 3 3 2 6 2s5 1 5 2.5L9 5.2 8.2 4H3.8L3 5.2zM3 6h6l1.5 4.5h-9z"/></svg>02 9364 2710</li>
        <li><svg viewBox="0 0 12 12"><path d="M1 4.5C1 3 3 2 6 2s5 1 5 2.5L9 5.2 8.2 4H3.8L3 5.2zM3 6h6l1.5 4.5h-9z"/></svg>02 8472 3159 (DIRECT)</li>
        <li><svg viewBox="0 0 12 12"><path d="M1 2.5h10v7H1zM1.6 3.1 6 6.5l4.4-3.4"/></svg>paul@qvlegal.com.au</li>
        <li><svg viewBox="0 0 12 12"><circle cx="6" cy="6" r="5"/></svg>www.qvlegal.com.au</li>
      </ul>
      <p class="address">Level 9, 7 Ferris Lane<br>Sydney NSW 2000</p>
    </div>
  </section>

  <section class="card card-back">
    <div class="back-brand">
      <span class="brand-square"></span>
      <span class="brand-name">QUAYVALE LEGAL</span>
    </div>
  </section>

</body>
</html>
```